Dietitian needs awesome business card

I need a contemporary design that's eye catching but professional.
My card is to given to doctors, specialists and patients alike.
I manage patients with chronic diseases
I have uploaded my logo and current business card, I would also like the other Certified Clinical Nutritionist logo incorporated into the design

Target Market(s)

Doctors, specialists and patients

Industry/Entity Type

Healthcare

Contact Information for Business Card

www.brightfieldnutrition.com.au
Ph: 0427 561 903
Fax: 6457 2183
email: marcus.k.diet@fernmail.com
Space on the back of the card with: Appointment date, Appointment time and appointment location

Font styles to use
Serif

Colors
fbee3e
876aae
ffc214

Requirements
Must have
• My Logo
• Certified Clinical Nutritionist Logo
• My 4 locations - Pinebrook Medical Centre, North Corrin Health, Hollis Medical, Ashcombe Doctors Surgery
Nice to have
• I like the colours in my current business card

```html
<!DOCTYPE html>
<html lang="en">
<head>
<meta charset="utf-8">
<title>Brightfield Nutrition &amp; Dietetics – Business Card</title>
<link href="https://fonts.googleapis.com/css2?family=Libre+Baskerville&family=Montserrat:wght@400;500&display=swap" rel="stylesheet">
<style>
  :root {
    --bg: #3a3a3c;
    --paper: #ffffff;
    --ink-black: #050505;
    --navy: #1f3f95;
    --brand-blue: #2b5fb0;
    --green: #3dbb3a;
    --lime: #b5d334;
    --sky: #2291d6;
    --orange: #f47a20;
    --white: #ffffff;
  }
  * { margin: 0; padding: 0; box-sizing: border-box; }
  html, body { width: 1200px; height: 900px; overflow: hidden; }
  body { background: var(--bg); position: relative; font-family: "Montserrat", sans-serif; }

  .card {
    position: absolute;
    left: 270px;
    width: 660px;
    height: 378px;
    border-radius: 22px;
    overflow: hidden;
  }

  /* ---------- Appointment side ---------- */
  .card-back { top: 50px; background: var(--paper); }
  .brand {
    position: absolute;
    display: flex;
    align-items: center;
    gap: 14px;
  }
  .brand-dot {
    width: 54px; height: 54px; border-radius: 50%;
    background: var(--brand-blue);
    flex: none;
  }
  .brand-name {
    font-family: "Libre Baskerville", serif;
    color: var(--brand-blue);
    line-height: 1.15;
    font-size: 24px;
  }
  .card-back .brand { left: 150px; top: 48px; }
  .tagline {
    position: absolute; left: 0; right: 0; top: 150px;
    text-align: center;
    font-family: "Libre Baskerville", serif;
    font-size: 16px; color: var(--navy);
  }
  .appointment-title {
    position: absolute; left: 0; right: 0; top: 190px;
    text-align: center;
    font-size: 20px; font-weight: 500; color: var(--green);
  }
  .field {
    position: absolute;
    display: flex; align-items: flex-end; gap: 6px;
    font-size: 16px; color: var(--navy);
  }
  .field-line { flex: 1; border-bottom: 1.5px solid var(--navy); height: 18px; }
  .field-date { left: 60px; top: 250px; width: 290px; }
  .field-time { left: 360px; top: 250px; width: 250px; }
  .field-location { left: 60px; top: 300px; width: 550px; }

  /* ---------- Contact side ---------- */
  .card-front { top: 470px; background: var(--ink-black); }
  .card-front .brand { left: 40px; top: 112px; }
  .bands { position: absolute; inset: 0; }
  .holder-name {
    position: absolute; right: 196px; top: 46px;
    font-family: "Libre Baskerville", serif;
    font-size: 22px; color: var(--sky);
  }
  .holder-name .surname { color: var(--white); }
  .name-rule {
    position: absolute; left: 300px; right: 190px; top: 86px;
    border-top: 1.5px solid var(--white);
  }
  .credential-badge {
    position: absolute; right: 40px; top: 40px;
    width: 136px; height: 96px;
    background: var(--orange);
  }
  .contact-rule {
    position: absolute; left: 40px; top: 218px; width: 380px;
    border-top: 1.5px solid var(--white);
  }
  .contacts {
    position: absolute; left: 40px; top: 230px;
    list-style: none;
    font-size: 16px; color: var(--white);
  }
  .contacts li { display: flex; align-items: center; gap: 12px; height: 24px; }
  .contacts svg { width: 13px; height: 13px; fill: var(--sky); flex: none; }
</style>
</head>
<body>

<section class="card card-back">
  <div class="brand">
    <span class="brand-dot"></span>
    <span class="brand-name">Brightfield<br>Nutrition &amp; Dietetics</span>
  </div>
  <p class="tagline">Certified Clinical Nutritionist, Nutritionist and Chef</p>
  <p class="appointment-title">Appointment:</p>
  <div class="field field-date">Date:<span class="field-line"></span></div>
  <div class="field field-time">Time:<span class="field-line"></span></div>
  <div class="field field-location">Location:<span class="field-line"></span></div>
</section>

<section class="card card-front">
  <svg class="bands" viewBox="0 0 660 378" aria-hidden="true">
    <polygon points="590,225 660,212 660,318 560,318" fill="var(--sky)"/>
    <polygon points="0,358 560,318 560,334 0,378" fill="var(--lime)"/>
  </svg>
  <p class="holder-name">Marcus <span class="surname">Kellaway</span></p>
  <div class="name-rule"></div>
  <div class="credential-badge" role="img" aria-label="Certified Clinical Nutritionist credential badge"></div>
  <div class="brand">
    <span class="brand-dot"></span>
    <span class="brand-name">Brightfield<br>Nutrition &amp; Dietetics</span>
  </div>
  <div class="contact-rule"></div>
  <ul class="contacts">
    <li><svg viewBox="0 0 24 24"><path d="M6.6 10.8a15 15 0 0 0 6.6 6.6l2.2-2.2c.3-.3.7-.4 1-.2 1.1.4 2.3.6 3.6.6.6 0 1 .4 1 1V20c0 .6-.4 1-1 1A17 17 0 0 1 3 4c0-.6.4-1 1-1h3.5c.6 0 1 .4 1 1 0 1.3.2 2.5.6 3.6.1.3 0 .7-.2 1z"/></svg>0427 561 903</li>
    <li><svg viewBox="0 0 24 24"><rect x="6" y="2" width="12" height="6"/><rect x="2" y="9" width="20" height="9" rx="2"/><rect x="6" y="15" width="12" height="7"/></svg>6457 2183</li>
    <li><svg viewBox="0 0 24 24"><path d="M2 5h20v14H2z M3 6l9 7 9-7" fill="none" stroke="var(--sky)" stroke-width="2"/></svg>marcus.k.diet@fernmail.com</li>
    <li><svg viewBox="0 0 24 24"><circle cx="12" cy="12" r="9" fill="none" stroke="var(--sky)" stroke-width="2"/><path d="M3 12h18M12 3c3 3 3 15 0 18M12 3c-3 3-3 15 0 18" fill="none" stroke="var(--sky)" stroke-width="1.5"/></svg>www.brightfieldnutrition.com.au</li>
  </ul>
</section>

</body>
</html>
```